New Business Card Design Project

Need a design that will create an impact / strong impression towards our clients for our business. We are in the lighting business and we do lighting retrofits for large commercial to industrial clientele.

Target Market(s)

Lighting Industry

Industry/Entity Type

Business

Font styles to use
Other font styles liked:
• we would like to use the font on our logo, not sure what it is though..

Requirements
Must have
• Our logo.
Nice to have
• We are open to suggestions that have to do with lighting.

```html
<!DOCTYPE html>
<html lang="en">
<head>
<meta charset="utf-8">
<title>Lumen Retrofit Co. — Business Card</title>
<link rel="stylesheet" href="https://fonts.googleapis.com/css2?family=Roboto:wght@400;500;700&family=Roboto+Condensed:wght@400;700&display=swap">
<style>
  :root {
    --stage: #e9e7e2;
    --card-dark: #262828;
    --card-dark-edge: #1c1d1d;
    --card-light: #f8f8f6;
    --green: #5cc33f;
    --green-deep: #1f6b2a;
    --text-light: #f2f2f2;
    --text-grey: #5a5a5a;
    --wash-green: #d6e8d6;
    --wash-grey: #d6dad6;
  }
  * { box-sizing: border-box; margin: 0; padding: 0; }
  html, body { width: 1200px; height: 911px; overflow: hidden; }
  body {
    background: var(--stage);
    display: flex;
    flex-direction: column;
    align-items: center;
    justify-content: center;
    gap: 40px;
    font-family: "Roboto", Arial, sans-serif;
  }
  .card {
    width: 700px;
    height: 400px;
    border-radius: 22px;
    position: relative;
    overflow: hidden;
    box-shadow: 0 10px 28px rgba(0,0,0,0.18);
  }

  /* Back: contact side */
  .card-back {
    background: linear-gradient(160deg, #303232 0%, var(--card-dark) 45%, var(--card-dark-edge) 100%);
    color: var(--text-light);
    display: flex;
    align-items: center;
    justify-content: center;
  }
  .contact-block {
    font-family: "Roboto Condensed", "Arial Narrow", sans-serif;
    font-size: 21px;
    line-height: 1.35;
    text-align: center;
  }
  .contact-name {
    color: var(--green);
    font-size: 30px;
    font-weight: 700;
    letter-spacing: 0.5px;
    text-transform: uppercase;
  }
  .contact-title {
    font-size: 22px;
    text-transform: uppercase;
    margin-bottom: 26px;
  }
  .contact-label { color: var(--green); font-weight: 700; }
  .contact-web {
    margin-top: 26px;
    color: var(--green);
    font-weight: 700;
    font-size: 22px;
    text-transform: uppercase;
  }

  /* Front: brand side */
  .card-front { background: var(--card-light); }
  .brand {
    position: absolute;
    top: 44px;
    left: 56px;
  }
  .brand-name {
    font-family: "Roboto", Arial, sans-serif;
    font-weight: 700;
    font-size: 46px;
    color: var(--green-deep);
    letter-spacing: 1px;
    text-transform: uppercase;
    display: flex;
    align-items: center;
    gap: 14px;
  }
  .brand-mark {
    width: 22px;
    height: 22px;
    border-radius: 50%;
    background: var(--green);
  }
  .brand-web {
    margin-top: 8px;
    font-size: 20px;
    color: var(--text-grey);
  }
  .light-wash {
    position: absolute;
    left: 0;
    bottom: 0;
    width: 700px;
    height: 230px;
    background: linear-gradient(180deg, rgba(214,232,214,0) 0%, var(--wash-green) 45%, var(--wash-grey) 100%);
  }
</style>
</head>
<body>

  <section class="card card-back" aria-label="Business card, contact side">
    <div class="contact-block">
      <div class="contact-name">Dana Whitfield</div>
      <div class="contact-title">CEO/Founder</div>
      <div class="contact-address">1420 Alder Court, Fairbanks, Alaska 99701</div>
      <div class="contact-phones">
        <span class="contact-label">P:</span> 555 214 7780
        <span class="contact-label">C:</span> 555 302 6619
        <span class="contact-label">F:</span> 555 871 4025
      </div>
      <div class="contact-email"><span class="contact-label">E:</span> dana@lumenretrofit.co</div>
      <div class="contact-web">www.lumenretrofitco.com</div>
    </div>
  </section>

  <section class="card card-front" aria-label="Business card, brand side">
    <div class="brand">
      <div class="brand-name"><span class="brand-mark"></span>Lumen Retrofit Co.</div>
      <div class="brand-web">www.lumenretrofitco.com</div>
    </div>
    <div class="light-wash" role="img" aria-label="Decorative graphic area in pale green and grey tones"></div>
  </section>

</body>
</html>
```